Billboard design 8x3M RAVU (Spanish company)

We´re located in the south of Spain. We run a local telecom company.
We sell Fiber optic, and mobile phone lines mainly.
The billboard will have to be in Spanish, I would like the price to be something you spot on first sight when passing by in the car.
Our company color is blue, like in our logo which I will add. I will also add a example from what we currently have.
The new offer should be:
1000 megas + 100Gigas movil con llamadas ilimitadas. (meaning 1000Mb fiber optic speed and 100Gb data and unlimited calls for 1 mobile line)
Our details are: phone line 958 47 6620
Website: ra-vu.es

```html
<!DOCTYPE html>
<html lang="es">
<head>
<meta charset="UTF-8">
<title>RAVU · Valla Fibra Óptica</title>
<link href="https://fonts.googleapis.com/css2?family=Poppins:wght@400;500;600;700;800&family=Big+Shoulders+Display:wght@700&display=swap" rel="stylesheet">
<style>
  :root {
    --page-bg: #e6e9ec;
    --panel-white: #f4f5f6;
    --navy: #0a2e44;
    --navy-mid: #0f5577;
    --sky: #2aa6dc;
    --brand-blue: #1f93c4;
    --ink: #0d3650;
    --accent: #f2a400;
    --white: #ffffff;
  }
  * { box-sizing: border-box; margin: 0; padding: 0; }
  html, body {
    width: 1200px; height: 900px; overflow: hidden;
    background: var(--page-bg);
    font-family: "Poppins", sans-serif;
  }
  .billboard {
    position: absolute; left: 40px; top: 238px;
    width: 1120px; height: 424px;
    display: flex;
    box-shadow: 0 6px 24px rgba(0,0,0,.18);
  }
  .brand-panel {
    position: relative;
    width: 309px; height: 100%;
    background: var(--panel-white);
  }
  .brand-name {
    position: absolute; left: 44px; top: 52px;
    display: flex; align-items: center; gap: 12px;
    font-weight: 800; font-size: 62px; letter-spacing: 2px;
    color: var(--brand-blue); line-height: 1;
  }
  .brand-dot {
    width: 20px; height: 20px; border-radius: 50%;
    background: var(--ink);
  }
  .services {
    position: absolute; left: 46px; top: 128px;
    font-weight: 600; font-size: 19px; color: var(--brand-blue);
    letter-spacing: -.2px;
  }
  .website {
    position: absolute; left: 0; right: 0; top: 310px;
    text-align: center;
    font-weight: 500; font-size: 15px; letter-spacing: 5px;
    color: var(--ink);
  }
  .phone {
    position: absolute; left: 46px; top: 332px;
    display: flex; align-items: center; gap: 8px;
    font-weight: 700; font-size: 31px; color: var(--ink);
  }
  .offer-panel {
    position: relative; flex: 1; height: 100%;
    background: linear-gradient(100deg, var(--navy) 0%, var(--navy-mid) 38%, var(--brand-blue) 68%, var(--sky) 100%);
    color: var(--white);
    overflow: hidden;
  }
  .headline {
    position: absolute; left: 36px; top: 56px;
    font-weight: 700; font-size: 40px; line-height: 1;
  }
  .rule { position: absolute; left: 36px; top: 134px; }
  .claim {
    position: absolute; left: 37px; top: 156px;
    font-weight: 500; font-size: 16px; line-height: 20px;
    letter-spacing: 1.4px; color: var(--accent);
  }
  .speed {
    position: absolute; left: 36px; top: 268px;
    font-weight: 800; font-size: 56px; line-height: 1;
    color: var(--accent); letter-spacing: -1px;
  }
  .speed small { font-size: 30px; letter-spacing: 0; }
  .mobile {
    position: absolute; left: 38px; top: 332px;
    display: flex; align-items: flex-end; gap: 14px;
  }
  .mobile-data { font-weight: 700; font-size: 29px; line-height: 1; }
  .mobile-data small { font-size: 18px; }
  .mobile-note { font-size: 13px; line-height: 14px; padding-bottom: 1px; }
  .price-box {
    position: absolute; left: 330px; top: 58px;
    width: 430px; height: 305px;
    border: 3px solid var(--white); border-radius: 28px;
  }
  .price { position: absolute; left: 28px; top: 34px; }
  .price-tag {
    position: absolute; left: -38px; top: 117px;
    width: 74px; height: 74px; border-radius: 50%;
    background: var(--accent);
    display: flex; align-items: center; justify-content: center;
    text-align: center;
    font-weight: 600; font-size: 17px; line-height: 18px; color: var(--white);
  }
</style>
</head>
<body>
  <div class="billboard">
    <section class="brand-panel">
      <div class="brand-name"><span>RAVU</span><span class="brand-dot"></span></div>
      <p class="services">Wifi | Fibra | Movil | Tv</p>
      <p class="website">www.ra-vu.es</p>
      <p class="phone">
        <svg width="16" height="26" viewBox="0 0 16 26" aria-hidden="true">
          <rect x="2" y="2" width="12" height="22" rx="2.5" fill="none" stroke="#f2a400" stroke-width="2.4"/>
          <line x1="6" y1="20" x2="10" y2="20" stroke="#f2a400" stroke-width="1.8"/>
        </svg>
        958 47 6620
      </p>
    </section>

    <section class="offer-panel">
      <h1 class="headline">Fibra Óptica</h1>
      <svg class="rule" width="80" height="4" viewBox="0 0 80 4" aria-hidden="true">
        <line x1="0" y1="2" x2="54" y2="2" stroke="#fff" stroke-width="2"/>
        <line x1="57" y1="2" x2="66" y2="2" stroke="#fff" stroke-width="2"/>
        <line x1="69" y1="2" x2="74" y2="2" stroke="#fff" stroke-width="2"/>
        <line x1="77" y1="2" x2="79" y2="2" stroke="#fff" stroke-width="2"/>
      </svg>
      <p class="claim">TU FIBRA + MÓVIL<br>AL MEJOR PRECIO</p>

      <p class="speed">1000<small>Mb</small></p>
      <div class="mobile">
        <p class="mobile-data">+ 100<small>Gb</small></p>
        <p class="mobile-note">Móvil con<br>llamadas ilimitadas</p>
      </div>

      <div class="price-box">
        <svg class="price" width="376" height="240" viewBox="0 0 376 240">
          <text x="0" y="234" textLength="376" lengthAdjust="spacingAndGlyphs"
                font-family="'Big Shoulders Display', sans-serif" font-weight="700"
                font-size="318" fill="#f7f7f4">18.45€</text>
        </svg>
        <div class="price-tag">por<br>sólo</div>
      </div>
    </section>
  </div>
</body>
</html>
```